PLUMA Project Roll Up Banner 85x200 cm (1:10, 1200 dpi)

PLUMA is a EU-funded project to promote female entrepreneurship networks. The project is developed by 9 partners from 7 different countries.
The banner is to be used throughout the project in exhibitions, conferences, roundtables, etc.
It has to include the following graphic elements, which cannot be modified beyond scaling:
- PLUMA logo
- EU logo (cannot be modified in any way, and cannot have any kind of background, but pure white).
- 9 partners logos
- Facebook link (with logo)
- LinkedIn link (with logo)
- Project's website (www.pluma-circle.example)
The text to be included:
Pioneering Ladies Undertaking Market Advances
PLUMA: Contributes to the strengthening of the links between women entrepreneurs and the mainstream of new technologies, educational, and training practices offered all over Europe.
GOOD PRACTICES: Compilation of EU projects promoting female entrepreneurship and ICT systems for learning, supporting, and training women entrepreneurs.
NETWORK: Strengthening of linkages between EU women entrepreneurs, project managers, learning communities, multipliers, and society to encourage a knowledge-sharing environment through the creation of the PLUMA circle.
ONE-STOP SHOP: Development of a multi-lingual EU online platform, where valuable an innovative EU learning opportunities can be found and accessed at one single place, as well as fostering new business opportunities by a Virtual Market.
The banner has to be attractive the modern female entrepreneur. It has to be easy to read, and present a fresh and exciting identity.
The banner has to include 5 additional centimetres on the top, and 10 on the bottom.
The last partner logo has been uploaded now.
Female entrepreneurs
Higher Educational Institutions
Government Female Representatives
Environment

```html
<!DOCTYPE html>
<html lang="en">
<head>
<meta charset="utf-8">
<title>PLUMA Roll Up Banner</title>
<link rel="stylesheet" href="https://fonts.googleapis.com/css2?family=Jura:wght@400;500&family=PT+Sans:wght@400&display=swap">
<style>
  :root{
    --orange:#f47b20;
    --orange-deep:#ee6f12;
    --blue:#363b97;
    --ink:#2b2b2b;
    --white:#ffffff;
    --grey:#8a8a8a;
    --display:"Jura", sans-serif;
    --body:"PT Sans", sans-serif;
  }
  *{margin:0;padding:0;box-sizing:border-box}
  html,body{width:1200px;height:3019px;overflow:hidden;background:var(--white)}
  .banner{position:relative;width:1200px;height:3019px;background:var(--white)}

  .top-band{position:absolute;left:0;top:0;width:1200px;height:70px;background:var(--orange)}

  .hero-photo{position:absolute;left:0;top:70px;width:1200px;height:1150px;
    background:
      linear-gradient(180deg,rgba(255,255,255,0) 70%,#fff 100%),
      radial-gradient(ellipse 30% 45% at 50% 55%,#f1ede8 0%,rgba(241,237,232,0) 100%),
      linear-gradient(90deg,#c9d5e3 0%,#e9e4df 30%,#f2efec 50%,#dfe3ea 72%,#b9c4d2 100%)}

  .brand-band{position:absolute;left:0;top:1343px;width:1200px;height:165px;
    background:linear-gradient(90deg,#fff 0%,#fff 38%,#f9c69b 60%,var(--orange) 100%)}
  .brand{position:absolute;left:80px;top:1330px;display:flex;align-items:center;gap:26px}
  .brand-mark{width:70px;height:70px;border-radius:50%;background:var(--blue)}
  .brand-name{font-family:var(--display);font-weight:500;font-size:96px;letter-spacing:4px;color:var(--blue);line-height:1}
  .brand-tagline{position:absolute;left:176px;top:1445px;font-family:var(--display);font-size:30px;color:var(--blue)}

  .content{position:absolute;left:0;top:1508px;width:1200px;height:1040px;background:var(--orange)}
  .headline{position:absolute;left:40px;top:30px;width:1120px;text-align:center;
    font-family:var(--display);font-weight:400;font-size:62px;line-height:68px;color:var(--white)}

  .pillar{position:absolute;left:0;width:1200px}
  .pillar-label{position:absolute;left:50px;font-family:var(--display);font-size:46px;line-height:48px;color:var(--white)}
  .pillar-text{position:absolute;left:319px;width:845px;font-family:var(--body);font-size:29px;line-height:38px;color:var(--white)}

  .partners{position:absolute;left:0;top:2548px;width:1200px;height:200px;background:var(--white)}
  .partner-row{position:absolute;left:0;width:1200px;display:flex;justify-content:center;align-items:center}
  .partner{display:flex;align-items:center;gap:10px;padding:0 22px;height:80px;border-left:2px solid #cfcfcf;
    font-family:var(--body);font-size:26px;color:var(--ink)}
  .partner:first-child{border-left:none}
  .partner .dot{width:34px;height:34px;background:var(--orange)}
  .partner .dot.blue{background:var(--blue)}
  .partner .dot.green{background:#8dbb2e}
  .partner .dot.grey{background:var(--grey)}

  .rule{position:absolute;left:0;top:2748px;width:1200px;height:10px;background:var(--orange)}
  .contacts{position:absolute;left:0;top:2758px;width:1200px;height:104px;background:var(--white);
    display:flex;justify-content:space-between;align-items:center;padding:0 50px;
    font-family:var(--body);font-size:30px;color:var(--ink)}
  .contact{display:flex;align-items:center;gap:16px}
  .contact .chip{width:36px;height:36px;background:var(--blue);border-radius:4px}
  .bottom-band{position:absolute;left:0;top:2862px;width:1200px;height:157px;background:var(--orange)}
</style>
</head>
<body>
<div class="banner">
  <div class="top-band"></div>

  <div class="hero-photo" role="img" aria-label="Photograph of a smiling businesswoman with crossed arms in front of four cheering colleagues"></div>

  <div class="brand-band"></div>
  <div class="brand">
    <span class="brand-mark"></span>
    <span class="brand-name">PLUMA</span>
  </div>
  <div class="brand-tagline">Women – Entrepreneurship – Networking</div>

  <section class="content">
    <h1 class="headline">Pioneering Ladies Undertaking<br>Market Advances</h1>

    <div class="pillar" style="top:279px">
      <div class="pillar-label" style="top:30px">PLUMA</div>
      <p class="pillar-text">Contributes to the strengthening of the links between women entrepreneurs and the mainstream of new technologies, educational, and training practices offered all over Europe.</p>
    </div>

    <div class="pillar" style="top:455px">
      <div class="pillar-label" style="top:20px">GOOD<br>PRACTICES</div>
      <p class="pillar-text">Compilation of EU projects promoting female entrepreneurship and ICT systems for learning, supporting, and training women entrepreneurs.</p>
    </div>

    <div class="pillar" style="top:625px">
      <div class="pillar-label" style="top:48px">NETWORK</div>
      <p class="pillar-text">Strengthening of linkages between EU women entrepreneurs, project managers, learning communities, multipliers, and society to encourage a knowledge-sharing environment through the creation of the PLUMA circle.</p>
    </div>

    <div class="pillar" style="top:814px">
      <div class="pillar-label" style="top:30px">ONE-STOP<br>SHOP</div>
      <p class="pillar-text">Development of a multi-lingual EU online platform, where valuable an innovative EU learning opportunities can be found and accessed at one single place, as well as fostering new business opportunities by a Virtual Market.</p>
    </div>
  </section>

  <section class="partners">
    <div class="partner-row" style="top:10px">
      <div class="partner"><span class="dot"></span>Tessera Civica</div>
      <div class="partner"><span class="dot green"></span>Brugstad</div>
      <div class="partner"><span class="dot green"></span>helinet.example</div>
      <div class="partner"><span class="dot blue"></span>Nordvik University</div>
    </div>
    <div class="partner-row" style="top:108px">
      <div class="partner"><span class="dot green"></span>Velatra</div>
      <div class="partner"><span class="dot grey"></span>FH Graustein</div>
      <div class="partner"><span class="dot blue"></span>orvena</div>
      <div class="partner"><span class="dot green"></span>novira consultancy</div>
      <div class="partner"><span class="dot blue"></span>Lifespan Study Scheme</div>
    </div>
  </section>

  <div class="rule"></div>
  <footer class="contacts">
    <div class="contact"><span class="chip"></span>/llp.pluma</div>
    <div class="contact">
      <svg width="38" height="38" viewBox="0 0 38 38" aria-hidden="true">
        <g fill="none" stroke="#3d8fd1" stroke-width="2.5">
          <circle cx="19" cy="19" r="16"/>
          <ellipse cx="19" cy="19" rx="7" ry="16"/>
          <line x1="3" y1="19" x2="35" y2="19"/>
          <line x1="6" y1="11" x2="32" y2="11"/>
          <line x1="6" y1="27" x2="32" y2="27"/>
        </g>
      </svg>
      www.pluma-circle.example
    </div>
    <div class="contact"><span class="chip"></span>/groups/PLUMA-4406218</div>
  </footer>
  <div class="bottom-band"></div>
</div>
</body>
</html>
```